Wordpress Web Design & Coding for velcorahealth.ca

We need a website for a new investment company that is visually grabbing and vibrant. We would like to see a web page that displays trust, growth and confidence. Needs to be responsive and mobile friendly for all browsers and coded for both Android & IOS.

Open to the number of pages and menu items. I selected 4 but if you feel the layout would work better with less I am open to this. Need to sell the people (management team/related businesses) and then show where the invested money will be going (upcoming projects).

Company Info:

Vel Cora is an investment company put together by a group of seasoned business professionals who have come together to combine decades of success in the real estate development, management, financing and medical services. The company will be a full service company offering turn key solutions for medical professionals.

Vel-Cora will focus on providing a full range of services via a group of distinct companies to deliver newly emerging needs of the medical community. The end goal will be to create complete solutions for individuals in the medical community. Our group has experience and success with the conceptualization, construction and financing of medical and dental clinic spaces. Vel-Cora Solutions will be established to accommodate all areas of the development and creation of clinics for medical professionals from building construction to equipment financing and administrations.

You can mention these companies and take photos from their websites. You can also use stock photos.

Our construction partner:
https://318bld.com/projects/

Our equipment leasing partner:
https://www.norvixa.com/

Our Management Team and medical partners

Gil Parish
https://www.ourfirmstance.ca/

Dietmar Vellasquin
https://www.gshdentalservices.com/about-us

PROPOSED PROJECTS (see attachment for details)
Pinegrove Business Park
Holtmere Business Park
Mt. Corwin Ridge Professional

Target Market(s)

Investors

Industry/Entity Type

Investment

Coding

Coded - Design and coding required

Number of Pages Required

4 page

Font styles to use
Sans Serif

Requirements
Must have
• Wordpress – must be both desktop and mobile friendly with fast page load speed
Ability to edit after ourselves in Wordpress
Attractive home page with logo etc.
Logo colours are: for the blue the pantone color is #0355a3
and for the green is #8cc63f

Sections, about us, what we do/services we provide, contact us

```html
<!DOCTYPE html>
<html lang="en">
<head>
<meta charset="utf-8">
<title>Vel-Cora Solutions</title>
<link rel="stylesheet" href="https://fonts.googleapis.com/css2?family=Poppins:wght@300;400;500;600&family=Roboto:wght@400;500&display=swap">
<style>
:root{
  --blue:#0355a3;
  --green:#8cc63f;
  --ink:#333;
  --muted:#777;
  --light:#f5f5f5;
  --footer:#2b2b2b;
  --line:#e6e6e6;
}
*{box-sizing:border-box;margin:0;padding:0}
html,body{width:1200px;height:3263px;overflow:hidden}
body{font-family:"Poppins",sans-serif;color:var(--ink);background:#fff;position:relative}
.abs{position:absolute}
.center{left:0;width:1200px;text-align:center}

/* header */
.site-header{position:absolute;top:0;left:0;width:1200px;height:93px;background:#fff;border-bottom:1px solid var(--line)}
.brand{position:absolute;left:110px;top:30px;display:flex;align-items:center;gap:10px;font-weight:600;font-size:24px;color:var(--blue);letter-spacing:.5px}
.brand-mark{width:22px;height:22px;background:var(--green)}
.main-nav{position:absolute;top:41px;left:620px;font-size:11.5px;font-weight:500;letter-spacing:.3px}
.main-nav a{color:#444;text-decoration:none;position:absolute;white-space:nowrap}
.main-nav a.active{color:var(--green)}

/* hero */
.hero{position:absolute;top:93px;left:0;width:1200px;height:592px;background:linear-gradient(110deg,#6faa4a 0%,#3f9a78 45%,#1f6fae 80%,#1c5aa4 100%)}
.hero h1{top:197px;font-size:52px;font-weight:500;color:#fff;letter-spacing:.5px}
.hero p{top:275px;font-size:21px;font-weight:400;color:#fff;line-height:35px}
.btn{display:inline-block;background:var(--green);color:#fff;font-weight:500;text-decoration:none}
.hero .btn{position:absolute;left:533px;top:362px;width:134px;height:39px;line-height:39px;text-align:center;font-size:13.5px}
.dots{position:absolute;top:564px;left:575px;display:flex;gap:8px}
.dots span{width:11px;height:11px;border-radius:50%;background:#fff}
.dots span.on{background:var(--blue)}

.section-title{font-size:27px;font-weight:500;color:#444}
.section-sub{font-size:13.5px;color:var(--muted);line-height:24px;font-weight:400}

/* services */
.service{position:absolute;top:852px;width:260px;text-align:center}
.service svg{display:block;margin:0 auto;width:88px;height:88px}
.service h3{font-size:18.5px;font-weight:500;margin-top:14px;color:#333}
.service p{font-size:13.5px;color:var(--muted);line-height:26px;margin-top:10px}

/* about */
.about-photo{position:absolute;top:1128px;left:0;width:614px;height:430px;background:linear-gradient(135deg,#3c3f44 0%,#6b6f72 45%,#b9bfc4 75%,#e2e6ea 100%)}
.about-text{position:absolute;top:1128px;left:652px;width:436px}
.about-text h2{margin-top:26px;font-size:27px;font-weight:500;color:#444}
.rule{width:42px;height:3px;background:var(--green)}
.about-text .rule{margin-top:10px}
.about-text p{font-size:13px;color:#666;line-height:25px;text-align:justify;margin-top:30px}
.about-text p + p{margin-top:25px}
.about-text .btn{position:absolute;top:367px;left:2px;width:97px;height:36px;line-height:36px;text-align:center;font-size:11.5px}

/* what we do */
.what{position:absolute;top:1558px;left:0;width:1200px;height:462px;background:linear-gradient(100deg,#4a4844 0%,#6e6a64 40%,#57534f 70%,#3d3b39 100%)}
.what h2{top:142px;font-size:40px;font-weight:500;color:#fff}
.what p{top:205px;font-size:24px;font-weight:500;color:#fff}
.play{position:absolute;left:563px;top:252px}

/* partners */
.partner{position:absolute;top:2163px;width:228px;height:224px;border:1px solid var(--line);box-shadow:0 0 4px rgba(0,0,0,.06);text-align:center;background:#fff}
.partner .logo-box{margin:9px 9px 0;height:106px;background:#f5f5f5;display:flex;align-items:center;justify-content:center;gap:8px;font-size:17px;font-weight:500;color:#3a3a3a}
.partner .logo-box i{width:14px;height:14px;display:block}
.partner h4{margin-top:21px;font-size:14px;font-weight:400;color:#333}
.partner p{font-size:12px;color:#666;line-height:24px;margin-top:6px;padding:0 14px}

/* team */
.team{position:absolute;top:2437px;left:0;width:1200px;height:439px;background:var(--light)}
.member{position:absolute;top:138px;width:472px;height:237px;background:#fff}
.member .photo{position:absolute;left:0;top:0;width:185px;height:237px}
.member .bio{position:absolute;left:212px;top:33px;width:236px}
.member h4{font-size:17px;font-weight:400;color:#444;letter-spacing:.3px}
.member .rule{margin-top:10px}
.member p{margin-top:15px;font-size:12.5px;color:#777;line-height:24px;text-align:justify}
.member a{display:block;margin-top:10px;font-size:12px;color:var(--green)}

/* footer */
.site-footer{position:absolute;top:2876px;left:0;width:1200px;height:387px;background:var(--footer);color:#fff}
.foot-brand{position:absolute;left:108px;top:42px;font-size:31px;font-weight:500}
.foot-about{position:absolute;left:109px;top:106px;width:336px;font-size:10.6px;line-height:23px;text-align:justify;color:#eee}
.foot-more{position:absolute;left:109px;top:220px;font-size:13px;font-weight:500;color:#fff}
.foot-h{position:absolute;top:50px;font-size:19px;font-weight:500}
.quick{position:absolute;left:506px;top:96px;list-style:none}
.quick li{position:relative;padding-left:37px;font-size:12.5px;font-weight:500;height:27.5px}
.quick li::before{content:"»";position:absolute;left:1px;top:-3px;font-size:14px}
.news-text{position:absolute;left:701px;top:86px;width:390px;font-family:"Roboto",sans-serif;font-size:15.5px;line-height:28px;color:#eee}
.email{position:absolute;left:702px;top:172px;width:385px;height:52px;background:#fff;color:#777;font-family:"Roboto",sans-serif;font-size:15px;line-height:52px;padding-left:16px}
.send{position:absolute;left:703px;top:241px;width:102px;height:40px;line-height:40px;text-align:center;background:var(--green);font-family:"Roboto",sans-serif;font-weight:500;font-size:17px}
.foot-rule{position:absolute;left:108px;top:304px;width:979px;height:1px;background:#444}
.copy{position:absolute;left:109px;top:342px;font-size:12.5px;color:#eee}
.social{position:absolute;left:876px;top:332px;display:flex;gap:7px}
.social span{width:36px;height:36px;border:2px solid #fff;border-radius:50%;display:block}
</style>
</head>
<body>

<header class="site-header">
  <div class="brand"><span class="brand-mark"></span>VEL-CORA</div>
  <nav class="main-nav">
    <a class="active" href="#" style="left:0">HOME</a>
    <a href="#" style="left:77px">ABOUT US</a>
    <a href="#" style="left:178px">WHAT WE DO</a>
    <a href="#" style="left:299px">SERVICES</a>
    <a href="#" style="left:393px">CONTACT US</a>
  </nav>
</header>

<section class="hero" role="img" aria-label="Glass office tower under a green to blue gradient">
  <h1 class="abs center">VELCORA SOLUTIONS</h1>
  <p class="abs center">Sed ut perspiciatis unde omnis iste natus error sit voluptatem<br>accusantium doloremque</p>
  <a class="btn" href="#">LEARN MORE</a>
  <div class="dots"><span></span><span class="on"></span><span></span></div>
</section>

<section class="services">
  <h2 class="abs center section-title" style="top:735px">OUR SERVICES</h2>
  <p class="abs center section-sub" style="top:782px">Vel-Cora will focus on providing a full range of services via a group of distinct &nbsp;newly<br>emerging needs of the medical community</p>

  <div class="service" style="left:146px">
    <svg viewBox="0 0 88 88" fill="none" stroke="#8cc63f" stroke-width="2.5">
      <rect x="4" y="10" width="80" height="56" rx="2"/>
      <path d="M4 56h80M38 66v12M50 66v12M28 80h32"/>
      <path d="M36 26l-8 7 8 7M52 26l8 7-8 7M47 22l-6 22"/>
    </svg>
    <h3>Development</h3>
    <p>Sed ut perspiciatis unde omnis iste natus error sit voluptatem accusan emque laudantium</p>
  </div>

  <div class="service" style="left:470px">
    <svg viewBox="0 0 88 88" fill="none" stroke="#0355a3" stroke-width="2.5">
      <rect x="30" y="8" width="28" height="18" rx="2"/>
      <rect x="6" y="62" width="24" height="18" rx="2"/>
      <rect x="32" y="62" width="24" height="18" rx="2"/>
      <rect x="58" y="62" width="24" height="18" rx="2"/>
      <path d="M44 26v18M18 44h52M18 44v18M44 44v18M70 44v18"/>
    </svg>
    <h3>Management</h3>
    <p>Sed ut perspiciatis unde omnis iste natus error sit voluptatem accusan emque laudantium</p>
  </div>

  <div class="service" style="left:802px">
    <svg viewBox="0 0 88 88" fill="none" stroke="#8cc63f" stroke-width="2.5">
      <circle cx="44" cy="44" r="36"/>
      <path d="M54 30q-4-6-11-6-10 0-10 8t11 9 11 9-10 8q-8 0-12-6M44 18v52"/>
    </svg>
    <h3>Financing</h3>
    <p>Sed ut perspiciatis unde omnis iste natus error sit voluptatem accusan emque laudantium</p>
  </div>
</section>

<div class="about-photo" role="img" aria-label="Business meeting reviewing charts on a clipboard with a calculator"></div>
<section class="about-text">
  <h2>ABOUT US</h2>
  <div class="rule"></div>
  <p>Vel Cora is an investment company put together by a group of seasoned business professionals who have come together to combine decades of success in the real estate development, management, financing and medical services. The company will be turn key solutions for medical professionals.</p>
  <p>Vel-Cora will focus on providing a full range of services via a group of distinct companies to deliver newly emerging needs of the medical community. The end goal will be to create complete solutions for individuals in the medical community.</p>
  <a class="btn" href="#">READ MORE</a>
</section>

<section class="what" role="img" aria-label="Business partners shaking hands across a table">
  <h2 class="abs center">WHAT WE DO</h2>
  <p class="abs center">Sed ut perspiciatis unde omnis iste natus error sit</p>
  <svg class="play" width="74" height="74" viewBox="0 0 74 74">
    <circle cx="37" cy="37" r="35" fill="none" stroke="#fff" stroke-width="2.5"/>
    <path d="M30 25l20 12-20 12z" fill="#fff"/>
  </svg>
</section>

<section class="partners">
  <h2 class="abs center section-title" style="top:2064px">OUR PARTNER</h2>
  <p class="abs center section-sub" style="top:2110px">Vel-Cora will focus on providing a full range of services via a group of distinct</p>

  <div class="partner" style="left:110px">
    <div class="logo-box"><i style="background:#1b3f8f"></i>318 BUILDERS INC.</div>
    <h4>Our Construction</h4>
    <p>Sed ut perspiciatis unde omnis iste natus error sit</p>
  </div>
  <div class="partner" style="left:360px">
    <div class="logo-box">NORVIXA</div>
    <h4>Our equipment leasing</h4>
    <p>Sed ut perspiciatis unde omnis iste natus error sit</p>
  </div>
  <div class="partner" style="left:610px">
    <div class="logo-box">firmstance</div>
    <h4>Gil Parish</h4>
    <p>Sed ut perspiciatis unde omnis iste natus error sit</p>
  </div>
  <div class="partner" style="left:859px">
    <div class="logo-box">GSH DENTAL</div>
    <h4>Dietmar Vellasquin</h4>
    <p>Sed ut perspiciatis unde omnis iste natus error sit</p>
  </div>
</section>

<section class="team">
  <h2 class="abs center section-title" style="top:28px">MANAGEMENT TEAM</h2>
  <p class="abs center section-sub" style="top:74px">Vel-Cora will focus on providing a full range of services via a group of distinct</p>

  <article class="member" style="left:111px">
    <div class="photo" role="img" aria-label="Portrait of a team member in a suit" style="background:linear-gradient(160deg,#cfd3d4,#6e7276 60%,#2f3236)"></div>
    <div class="bio">
      <h4>ALDEN MORAY</h4>
      <div class="rule"></div>
      <p>Sed ut perspiciatis unde omnis iste natus error sit voluptatem accusa nti um dolore mque laudantium, totam dicta sunt explicabo.</p>
      <a href="#">Read More</a>
    </div>
  </article>

  <article class="member" style="left:614px">
    <div class="photo" role="img" aria-label="Portrait of a team member in an office" style="background:linear-gradient(160deg,#c9d6e3,#8a7062 55%,#3d3835)"></div>
    <div class="bio">
      <h4>DIETMAR VELLASQUIN</h4>
      <div class="rule"></div>
      <p>Sed ut perspiciatis unde omnis iste natus error sit voluptatem accusa nti um dolore mque laudantium, totam dicta sunt explicabo.</p>
      <a href="#">Read More</a>
    </div>
  </article>
</section>

<footer class="site-footer">
  <div class="foot-brand">Velcora Solutions</div>
  <p class="foot-about">Sed ut perspiciatis unde omnis iste natus error sit volupta-tem accusantium doloremque laudantium, totam rem aperiam, eaque ipsa quae ab illo inventore veritatis et quasi architecto beatae vitae dicta sunt explicabo.</p>
  <a class="foot-more" href="#">READ MORE</a>

  <div class="foot-h" style="left:506px">QUICK LINKS</div>
  <ul class="quick">
    <li>HOME</li><li>ABOUT US</li><li>WHAT WE DO</li><li>SERVICES</li><li>CONTACT US</li>
  </ul>

  <div class="foot-h" style="left:700px">NEWSLETTER SUBSCRIPTION</div>
  <p class="news-text">Quillmark was founded in 2010 as a website dedicated to Gasoline Culture and all it entails</p>
  <div class="email">Email :</div>
  <div class="send">SEND</div>

  <div class="foot-rule"></div>
  <p class="copy">© Copyrights 2020-Velcora Solutions.All Rights Reserved.</p>
  <div class="social"><span></span><span></span><span></span><span></span><span></span></div>
</footer>

</body>
</html>
```